Need a stunning home page for Car rental company

For a client, I need a slick and sumber home page design. It is a small, local car rental company, with a handful of cars available for rent.
Selling points: affordable lease, availability, always clean cars
The design should be:
- flat and modern
- no, or very few animations/sliders
- CTA: booking form for renting a car.
- 3 featured cars with images and facts (see website) with button to read more about the car.
- fullscreen background video can be an option
- main colour: #efba01
The site is under construction here:
http://solvikutleie.hammerlia.no/
Delivery requirements:
I need a layered & well organised PSD file delivered.

```html
<!DOCTYPE html>
<html lang="no">
<head>
<meta charset="utf-8">
<title>Solvik Utleie – Hjem</title>
<link href="https://fonts.googleapis.com/css2?family=Arimo:wght@400;700&display=swap" rel="stylesheet">
<style>
:root{
  --brand:#efba01;
  --brand-dark:#c99a00;
  --ink:#111111;
  --white:#ffffff;
  --card:#f4f4f4;
  --muted:#333333;
}
*{margin:0;padding:0;box-sizing:border-box}
html,body{width:1071px;height:1200px;overflow:hidden;background:var(--white)}
body{font-family:"Arimo",Arial,sans-serif;color:var(--ink);position:relative}
.site-header{position:absolute;left:0;top:0;width:1071px;height:87px;background:var(--white)}
.brand{position:absolute;left:95px;top:44px;display:flex;align-items:center;gap:8px;font-weight:700;font-size:19px;letter-spacing:2px;color:var(--muted)}
.brand-mark{width:12px;height:12px;background:var(--brand)}
.hotline{position:absolute;right:88px;top:18px;font-size:12px;font-weight:700;color:var(--brand)}
.hotline span{color:var(--ink);font-weight:400}
.main-nav{position:absolute;right:88px;top:50px;display:flex;gap:31px;font-size:13px;font-weight:700}
.main-nav a{color:var(--ink);text-decoration:none}
.main-nav a.active{color:var(--brand)}
.hero-band{position:absolute;left:0;top:87px;width:1071px;height:407px;background:var(--brand)}
.slider{position:absolute;left:89px;top:31px;width:894px;height:270px;background:var(--white)}
.slider h1{position:absolute;left:33px;top:122px;font-size:21px;font-weight:700;color:#2a2a2a}
.cta{position:absolute;left:33px;top:158px;width:189px;height:35px;background:var(--brand-dark);color:var(--white);font-size:12.5px;font-weight:700;display:flex;align-items:center;justify-content:center}
.dots{position:absolute;left:32px;top:209px;display:flex;gap:4px}
.dots i{width:9px;height:9px;border-radius:50%;background:var(--ink)}
.dots i.on{background:var(--brand-dark)}
.hero-photo{position:absolute;right:36px;top:40px;width:410px;height:200px;border-radius:40% 45% 20% 25%;background:radial-gradient(ellipse at 55% 45%,#e8283a 0%,#b3121f 55%,#ffffff 80%)}
.welcome{position:absolute;left:0;top:319px;width:1071px;text-align:center}
.welcome h2{font-size:16px;font-weight:700;color:#222}
.welcome p{width:900px;margin:13px auto 0;font-size:12px;line-height:20px;color:var(--white)}
.featured{position:absolute;left:0;top:494px;width:1071px;height:614px;background:linear-gradient(100deg,#a8c060 0%,#d7e0a8 25%,#c9c9c9 55%,#6d6d6d 75%,#2b2b2b 100%)}
.featured h2{position:absolute;left:0;top:28px;width:1071px;text-align:center;font-size:21px;font-weight:700;color:var(--white);text-shadow:0 1px 3px rgba(0,0,0,.5)}
.car-card{position:absolute;top:71px;width:280px;height:494px;background:var(--card);padding:0 16px}
.car-card h3{margin-top:26px;font-size:12.5px;font-weight:700}
.car-photo{margin-top:9px;width:248px;height:135px}
.price-bar{width:248px;height:42px;background:var(--brand);color:var(--white);display:flex;justify-content:space-between;align-items:center;padding:0 8px 0 15px;font-size:12.5px;font-weight:700}
.specs{margin-top:12px;width:248px;font-size:12.5px;font-weight:700;border-collapse:collapse}
.specs td{height:27px}
.specs td:last-child{width:42px}
.read-more{position:absolute;left:49px;top:436px;width:182px;height:38px;background:var(--brand);color:var(--white);font-size:12.5px;font-weight:700;display:flex;align-items:center;justify-content:center}
.site-footer{position:absolute;left:0;top:1108px;width:1071px;height:92px}
.copyright{position:absolute;left:98px;top:38px;font-size:12.5px;font-weight:700}
.social{position:absolute;left:929px;top:37px;display:flex;gap:22px}
.social i{width:22px;height:22px;border-radius:50%;background:var(--brand)}
.version{position:absolute;left:1026px;top:40px;font-size:12px}
</style>
</head>
<body>
<header class="site-header">
  <div class="brand"><span class="brand-mark"></span>SOLVIK UTLEIE</div>
  <div class="hotline">Spørsmål? Ring Oss <span>91234567</span></div>
  <nav class="main-nav">
    <a class="active" href="#">Hjem</a><a href="#">Bilparken vår</a><a href="#">Tjenester</a><a href="#">Kontakt oss</a><a href="#">Blog</a><a href="#">Page templates</a><a href="#">About us</a>
  </nav>
</header>

<section class="hero-band">
  <div class="slider">
    <h1>We Are A Car Rental Company</h1>
    <div class="cta">A booking form to rent a car</div>
    <div class="dots"><i class="on"></i><i></i><i></i><i></i></div>
    <div class="hero-photo" role="img" aria-label="Red sedan car on white background"></div>
  </div>
  <div class="welcome">
    <h2>Velkommen til Solvik Utleie – Havøy</h2>
    <p>Solvik utleie er en bilpark på Havøy, og leier ut varebiler og personbiler til deg som trenger en ekstrabil til flytting, ferie, bytur eller hva det måtte være. Vi er uslåelige på service, og mest sannsynlig også på pris. Og du kan stole på at bilen du får fra oss er både ren og pen!</p>
  </div>
</section>

<section class="featured" role="img" aria-label="Motion-blurred photo of a car wheel on a road">
  <h2>Featured Cars</h2>

  <article class="car-card" style="left:89px">
    <h3>Featured Car 1</h3>
    <div class="car-photo" role="img" aria-label="White convertible car" style="background:radial-gradient(ellipse at 50% 55%,#d9d9d9 0%,#f2f2f2 45%,#ffffff 70%)"></div>
    <div class="price-bar"><span>Pris per døgn</span><span>kr 600</span></div>
    <table class="specs">
      <tr><td>BiltypeVarebil</td><td>Varebil</td></tr>
      <tr><td>Maks. pers</td><td>2</td></tr>
      <tr><td>Ant. dører</td><td>5</td></tr>
      <tr><td>Min. sjåføralder</td><td>21</td></tr>
      <tr><td>Girtype</td><td>II</td></tr>
      <tr><td>Klimaanlegg?</td><td>Ja</td></tr>
      <tr><td>Ubegrenset km?</td><td>Nei</td></tr>
    </table>
    <div class="read-more">Read More About The Car</div>
  </article>

  <article class="car-card" style="left:397px">
    <h3>Featured Car 1</h3>
    <div class="car-photo" role="img" aria-label="Red compact family car" style="background:radial-gradient(ellipse at 50% 55%,#e0301f 0%,#f08070 40%,#ffffff 70%)"></div>
    <div class="price-bar"><span>Pris per døgn</span><span>kr 600</span></div>
    <table class="specs">
      <tr><td>BiltypeVarebil</td><td>Varebil</td></tr>
      <tr><td>Maks. pers</td><td>2</td></tr>
      <tr><td>Ant. dører</td><td>5</td></tr>
      <tr><td>Min. sjåføralder</td><td>21</td></tr>
      <tr><td>Girtype</td><td>II</td></tr>
      <tr><td>Klimaanlegg?</td><td>Ja</td></tr>
      <tr><td>Ubegrenset km?</td><td>Nei</td></tr>
    </table>
    <div class="read-more">Read More About The Car</div>
  </article>

  <article class="car-card" style="left:704px">
    <h3>Featured Car 1</h3>
    <div class="car-photo" role="img" aria-label="Orange sports car" style="background:radial-gradient(ellipse at 50% 55%,#f7890f 0%,#f9b870 40%,#ffffff 70%)"></div>
    <div class="price-bar"><span>Pris per døgn</span><span>kr 600</span></div>
    <table class="specs">
      <tr><td>BiltypeVarebil</td><td>Varebil</td></tr>
      <tr><td>Maks. pers</td><td>2</td></tr>
      <tr><td>Ant. dører</td><td>5</td></tr>
      <tr><td>Min. sjåføralder</td><td>21</td></tr>
      <tr><td>Girtype</td><td>II</td></tr>
      <tr><td>Klimaanlegg?</td><td>Ja</td></tr>
      <tr><td>Ubegrenset km?</td><td>Nei</td></tr>
    </table>
    <div class="read-more">Read More About The Car</div>
  </article>
</section>

<footer class="site-footer">
  <div class="copyright">© Solvik Utleie 2014. All rights reserved</div>
  <div class="social"><i></i><i></i></div>
  <div class="version">SV</div>
</footer>
</body>
</html>
```